Plate of the Raven: Half-Page Magazine Ad

advertisement in a travel magazine for a casual/fine dining restaurant in the heart of Whitehorse, Yukon
Needs to say that it is located in the Stonefield Hotel, 247 Larch Avenue.

Northern inspired cuisine
plateoftheraven.example

Don't need to use all the pictures

Dimensions: ad is a half-page, dimensions are 7.25" x 4.8".

Target Market(s)

Upscale dining, corporate travellers

Industry/Entity Type

Restaurant

Colors
0054AA
0677BA
7BADD7
CADEEF
E8F1F8
0094D4
00A9DD
6FCCEA
C7EBF8
E9F6FB
00AB8E
00BBA5
67D7C9
C6EFE9
E9F9F6

Requirements
Must have
• Restaurant logo
Nice to have
• Simple, clean design with upscale feel

```html
<!DOCTYPE html>
<html lang="en">
<head>
<meta charset="utf-8">
<title>Plate of the Raven – Half-Page Magazine Ad</title>
<link rel="stylesheet" href="https://fonts.googleapis.com/css2?family=Cinzel:wght@400;600;700&family=Poppins:wght@300;400;500;700&display=swap">
<style>
  :root {
    --canvas-grey: #808080;
    --ink: #111111;
    --ink-soft: #777777;
    --panel-white: rgba(255, 255, 255, 0.9);
    --band-grey: #e6e3e1;
    --label-black: #050505;
    --paper-white: #ffffff;
    --food-brown: #7a3d12;
    --food-amber: #c8741e;
    --food-dark: #3b1f0c;
    --food-green: #56702f;
  }
  * { margin: 0; padding: 0; box-sizing: border-box; }
  html, body {
    width: 1200px;
    height: 2550px;
    overflow: hidden;
    background: var(--canvas-grey);
  }
  .ad {
    position: absolute;
    left: 100px;
    top: 627px;
    width: 1000px;
    height: 1295px;
    box-shadow: 0 12px 30px rgba(0, 0, 0, 0.35);
    overflow: hidden;
  }
  .ad__backdrop {
    position: absolute;
    inset: 0;
    background:
      radial-gradient(circle at 20% 25%, rgba(86, 112, 47, 0.75) 0, rgba(86, 112, 47, 0) 22%),
      radial-gradient(circle at 85% 10%, rgba(70, 110, 170, 0.55) 0, rgba(70, 110, 170, 0) 20%),
      radial-gradient(circle at 70% 80%, var(--food-amber) 0, rgba(200, 116, 30, 0) 45%),
      radial-gradient(circle at 30% 70%, #b3581a 0, rgba(179, 88, 26, 0) 45%),
      linear-gradient(160deg, var(--food-dark) 0%, var(--food-brown) 45%, var(--food-amber) 75%, var(--food-brown) 100%);
  }
  .ad__panel {
    position: absolute;
    inset: 0;
    width: 1000px;
    height: 1295px;
  }
  .ad__content {
    position: absolute;
    inset: 0;
    text-align: center;
    color: var(--ink);
  }

  .brand {
    position: absolute;
    left: 340px;
    top: 125px;
    display: flex;
    align-items: center;
    gap: 26px;
  }
  .brand__mark {
    width: 150px;
    height: 150px;
    border-radius: 50%;
    background: #d9d6d3;
  }
  .brand__name {
    font-family: 'Cinzel', serif;
    font-weight: 700;
    font-size: 50px;
    line-height: 0.98;
    color: var(--ink);
    text-align: left;
  }

  .headline {
    position: absolute;
    left: 0;
    right: 0;
    top: 408px;
    font-family: 'Cinzel', serif;
  }
  .headline__lead {
    display: block;
    font-weight: 600;
    font-size: 82px;
    line-height: 1;
    color: var(--ink);
    letter-spacing: 1px;
  }
  .headline__main {
    display: block;
    font-weight: 400;
    font-size: 88px;
    line-height: 1;
    color: var(--ink-soft);
    margin-top: -4px;
  }
  .headline__place {
    display: block;
    font-family: 'Poppins', sans-serif;
    font-weight: 400;
    font-size: 34px;
    line-height: 1.2;
    margin-top: 8px;
    color: var(--ink);
  }
  .headline__place strong { font-weight: 700; }

  .dish-strip {
    position: absolute;
    left: 108px;
    top: 687px;
    width: 783px;
    height: 193px;
    display: flex;
    gap: 7px;
  }
  .dish-strip__photo { flex: 1; height: 100%; }
  .dish-strip__photo--board {
    background: linear-gradient(135deg, #2b2b2b 0%, #8e2a2e 35%, #e2c15a 65%, #314021 100%);
  }
  .dish-strip__photo--bowl {
    background: radial-gradient(circle at 50% 45%, #6f8f3a 0, #b0803e 45%, #3a2f28 100%);
  }
  .dish-strip__photo--crab {
    background: linear-gradient(135deg, #d9733c 0%, #e7b04a 45%, #c8a637 60%, #3d2f3c 100%);
  }

  .cuisine-label {
    position: absolute;
    left: 202px;
    top: 864px;
    width: 592px;
    height: 47px;
    background: var(--label-black);
    color: var(--paper-white);
    font-family: 'Cinzel', serif;
    font-weight: 600;
    font-size: 24px;
    letter-spacing: 6px;
    line-height: 47px;
  }

  .location {
    position: absolute;
    left: 0;
    right: 0;
    top: 940px;
  }
  .location__pin { display: block; margin: 0 auto; width: 22px; height: 28px; }
  .location__address {
    font-family: 'Poppins', sans-serif;
    font-weight: 400;
    font-size: 33px;
    line-height: 1.2;
    color: #2a2a2a;
    margin-top: 2px;
  }

  .hours-band {
    position: absolute;
    left: 163px;
    top: 1053px;
    width: 683px;
    height: 49px;
    background: var(--band-grey);
    font-family: 'Poppins', sans-serif;
    font-weight: 300;
    font-size: 24px;
    letter-spacing: 4px;
    line-height: 49px;
    color: #333333;
  }
  .hours-band strong { font-weight: 700; color: var(--ink); }

  .web-address {
    position: absolute;
    left: 0;
    right: 0;
    top: 1142px;
    font-family: 'Poppins', sans-serif;
    font-weight: 400;
    font-size: 22px;
    letter-spacing: 3px;
    color: #444444;
  }
</style>
</head>
<body>
  <div class="ad">
    <div class="ad__backdrop" role="img" aria-label="Softly blurred close-up photograph of a plated northern dish in warm amber and brown tones"></div>

    <svg class="ad__panel" viewBox="0 0 1000 1295" aria-hidden="true">
      <path d="M125 65 H875 A75 75 0 0 0 950 140 V1158 A75 75 0 0 0 875 1233 H125 A75 75 0 0 0 50 1158 V140 A75 75 0 0 0 125 65 Z" fill="rgba(255,255,255,0.9)"/>
    </svg>

    <div class="ad__content">
      <div class="brand">
        <span class="brand__mark"></span>
        <span class="brand__name">PLATE<br>OF THE<br>RAVEN</span>
      </div>

      <h1 class="headline">
        <span class="headline__lead">A FINE DINING</span>
        <span class="headline__main">RESTAURANT</span>
        <span class="headline__place">IN THE HEART OF <strong>WHITEHORSE YUKON</strong></span>
      </h1>

      <div class="dish-strip">
        <div class="dish-strip__photo dish-strip__photo--board" role="img" aria-label="Charcuterie board with cured meats, cheese and pickles"></div>
        <div class="dish-strip__photo dish-strip__photo--bowl" role="img" aria-label="Bowl of pasta topped with microgreens and shaved cheese"></div>
        <div class="dish-strip__photo dish-strip__photo--crab" role="img" aria-label="Crab claw plate with salad and a bowl of soup"></div>
      </div>
      <div class="cuisine-label">NORTHERN INSPIRED CUISINE</div>

      <div class="location">
        <svg class="location__pin" viewBox="0 0 22 28" aria-hidden="true">
          <path d="M11 1 C5.5 1 1.5 5 1.5 10.3 C1.5 17 11 27 11 27 C11 27 20.5 17 20.5 10.3 C20.5 5 16.5 1 11 1 Z" fill="#111"/>
          <circle cx="11" cy="10.3" r="3.6" fill="#fff"/>
        </svg>
        <p class="location__address">Stonefield Hotel, 247 Larch Avenue</p>
      </div>

      <div class="hours-band">OPEN EVENINGS WITH A <strong>SUMMER PATIO</strong></div>

      <p class="web-address">www.plateoftheraven.example</p>
    </div>
  </div>
</body>
</html>
```